Bold, Modern, Clean "Kestrelwaymassage.com" website

Why we stand out?
We are a male and female mobile massage team. Our names are Paul and Lina. 
Kestrel Way is a Seattle based mobile massage service. Our massage is offered to the community with a goal of facilitating balance within each individual. We specialize in integrated Pain management, and sports/medical massage therapy. Every client's first assessment is attended by our male and female massage therapist team. Depending on the goals identified for an individual determines which therapist will be assigned to provide treatment, if not both.

Our passion...
Here at Kestrel Way, we have a great passion for Postural Resoration and how it is integrated into an individual's Massage treatment. We pride ourselves in being natural facilitators of healing, which takes the ego of the therapist out of the client's healing process. We strive to deliver the best massage possible by including modalities such as Neuromuscular, Myofascial release, spontaneous muscle release, postural restoration, orthopedic, and medical massage.

Our education...

We are both Graduates of Venmora, school of massage therapy. We have continuing education in medical massage, myofacial release, trigger point therapy, postural restoration, anatomy, and spontaneous muscle release. Lina is also a Certified Yoga Instructor, which amplifies her experience with flexibility and strength as it pertains to each individual. Paul's passion is Massage, stretching, and strength training to encourage postural restoration and realignment.

Our rates-

Our rates are $75/ 60 minutes, $95/ 90 minutes, and $120/ 120 minutes.

Education-
Both Lina and I worked as behavioral health professionals that specialized in life skills mentoring for youth who had experienced different types of trauma. This led us both to want to help others in a different environment, where individuals can be empowered to take responsibility over their own healing. To us, massage is a type of manipulation physical therapy, that encourages healing on many levels.

Advice to any massage client-
The most important thing to 'us', as Licenced providers is to get you on to our table to show you our skills. But a good therapist never forgets that it's not about what we do for you, but what we can facilitate for you. Your health and healing has nothing to do with us. It is yours, not ours. Identify what your goals are with any Therapist, and know what the end looks like. Progress should be tangible, such as range of motion, and decreased pain.

Lina and Paul at Kestrel Way are awesome! I recently had open heart surgery, and Lina worked on me to increase my range of motion while helping with the pinched nerve from my arm being in the same position for so long during my surgery. My wife drives a lot for work, and Paul has helped decrease her neck and lower back pain immensely. They are seriously the best therapists I have ever worked with. I would recommend them to anyone who needs anything from stress relief to a medical massage treatment. They are professional, up beat, easy going, and always on time. And, I love that they meet us where ever we like! We did a staycation recently, where they came to our hotel to give us relaxation massages. Although usually they come to our home, where we focus on pain related issues. We will continue to work with them for a long, long time.

Target Market(s)

Mobile massage therapy clients

Industry/Entity Type

Massage Therapy

Coding

Coded - Design and coding required

Number of Pages Required

1 page

Font styles to use
Serif
Sans Serif

Requirements
Must have
• Please add or remove any information that would help the presentation of our website. Our logo is posted below, please include into the website.
• Please include a contact field that includes, kestrelwaymassage@fernmail.net,
• (206) 555-0148
• We have also included our own stock photos, as well as a photo of Paul and Lina. Please include a cropped photo of both massage therapists.

```html
<!DOCTYPE html>
<html lang="en">
<head>
<meta charset="utf-8">
<title>Kestrel Way Massage</title>
<link href="https://fonts.googleapis.com/css2?family=Open+Sans:ital,wght@0,400;0,600;0,700;1,400&display=swap" rel="stylesheet">
<style>
:root{
  --navy:#272d69;
  --navy-deep:#1c2258;
  --blue:#1279b2;
  --blue-dark:#0c4f86;
  --ink:#444;
  --muted:#666;
  --light-bg:#f2f2f2;
  --footer:#2d2d2d;
  --white:#fff;
}
*{margin:0;padding:0;box-sizing:border-box}
html,body{width:682px;height:1200px;overflow:hidden;background:#fff}
body{font-family:"Open Sans",Arial,sans-serif;color:var(--ink);position:relative}
.abs{position:absolute}

.top-bar{left:0;top:0;width:682px;height:22px;background:var(--navy);color:#fff;font-size:6.5px}
.top-bar .item{position:absolute;top:7px;display:flex;align-items:center;gap:5px;white-space:nowrap}
.top-bar .divider{position:absolute;left:620px;top:4px;width:1px;height:14px;background:#fff}

.header{left:0;top:22px;width:682px;height:47px;background:#fff}
.nav{position:absolute;top:20px;font-size:7.5px;color:#555;letter-spacing:.2px}
.nav.active{color:var(--blue)}

.brand{left:48px;top:9px;width:76px;height:76px;border-radius:50%;background:var(--navy);border:4px solid #fff;box-shadow:0 0 0 1px #ccd;display:flex;align-items:center;justify-content:center;color:#fff;font-weight:700;font-size:11px;text-align:center;line-height:1.1;z-index:3}

.hero{left:0;top:69px;width:682px;height:273px;background:linear-gradient(100deg,#3a1f17 0%,#6b3a26 35%,#8a5236 55%,#4a3a36 80%,#2e2c30 100%)}
.hero-title{left:48px;top:145px;font-size:24px;font-weight:700;color:#fff;letter-spacing:.3px}
.hero-title span{color:#2a8ec8}
.hero-text{left:50px;top:185px;width:290px;font-size:6.8px;line-height:13.5px;color:#fff}
.hero-btn{left:50px;top:239px;width:126px;height:26px;border:1px solid #fff;color:#fff;font-size:7.5px;font-weight:600;display:flex;align-items:center;justify-content:center}
.dots{left:316px;top:323px;display:flex;gap:2px}
.dots span{width:8px;height:8px;border-radius:50%;border:1px solid #fff}
.dots span.on{background:var(--blue);border-color:var(--blue)}

.contact-form{left:447px;top:99px;width:186px;height:219px;background:rgba(30,30,35,.75)}
.contact-form .head{height:30px;background:var(--blue);color:#fff;font-size:12px;display:flex;align-items:center;justify-content:center}
.field{position:absolute;left:15px;width:158px;height:22px;background:#fff;border-radius:2px;font-size:6px;font-style:italic;color:#555;padding:7px 6px}
.field i{color:#d22;font-style:normal}
.submit{position:absolute;left:15px;top:183px;width:66px;height:26px;background:var(--blue);color:#fff;font-size:7.5px;font-weight:700;display:flex;align-items:center;justify-content:center;gap:3px}

.welcome{left:0;top:342px;width:682px;height:312px;background:var(--light-bg)}
.section-title{position:absolute;left:0;width:682px;text-align:center;font-size:13px;font-weight:600;color:#444;letter-spacing:.2px}
.section-text{position:absolute;left:108px;width:466px;text-align:center;font-size:6.4px;line-height:13.5px;color:var(--muted)}

.card{position:absolute;top:84px;width:139px;height:207px;color:#fff;overflow:hidden}
.card .photo{height:104px;background:linear-gradient(160deg,#e7d7cb,#c99a80)}
.card.navy .body{background:linear-gradient(#2a3170,var(--navy-deep))}
.card.blue .body{background:linear-gradient(#1683bd,#0d5d94)}
.card .body{height:103px;text-align:center;padding-top:14px}
.card h3{font-size:9.5px;font-weight:600}
.card p{font-size:6.3px;line-height:13.5px;margin:6px 12px 0;height:41px}
.card .more{font-size:7px;font-weight:700;margin-top:6px}

.rates{left:0;top:654px;width:682px;height:144px;background:#fff}
.rate-line{position:absolute;left:0;width:682px;top:93px;text-align:center;font-size:13.6px;color:#555}
.rate-line b{color:var(--blue);font-weight:600}

.reviews{left:0;top:798px;width:682px;height:181px;background:linear-gradient(#106eab,#0b3268)}
.reviews .section-text{color:#e6eef6}
.avatar{position:absolute;top:80px;width:56px;height:56px;border-radius:50%;background:linear-gradient(#d9c6b8,#9a7a66);border:2px solid #fff}
.reviewer{position:absolute;top:141px;width:90px;text-align:center;font-size:5.6px;font-weight:700;color:#f0b43a}
.stars{position:absolute;top:148px;width:90px;text-align:center;font-size:7px;color:#fff;letter-spacing:.5px}
.quote{position:absolute;top:82px;width:190px;height:60px;background:#fff;font-size:6px;font-style:italic;line-height:12.8px;color:#888;padding:8px 12px 0 22px}
.quote::before{content:"";position:absolute;left:-5px;top:25px;border:5px solid transparent;border-left:0;border-right-color:#fff}
.quote .q{position:absolute;font-style:normal;font-size:13px;color:#999;font-family:Georgia,serif}

.news{left:0;top:979px;width:682px;height:157px;background:#fff}
.news h2{position:absolute;left:58px;top:22px;font-size:13.5px;font-weight:600;color:#444}
.news .thumb{position:absolute;left:54px;top:50px;width:103px;height:83px;border:1px solid #ddd;padding:3px;background:#fff}
.news .thumb div{width:100%;height:100%;background:linear-gradient(#e4e6ea,#c6b3a4)}
.news h3{position:absolute;left:173px;top:55px;font-size:9.6px;font-weight:600;color:var(--blue)}
.news p{position:absolute;left:173px;top:76px;width:450px;font-size:6.2px;line-height:12px;color:var(--muted)}
.news .date{position:absolute;left:173px;top:117px;font-size:6.8px;color:var(--navy);display:flex;align-items:center;gap:2px}

.footer{left:0;top:1136px;width:682px;height:64px;background:var(--footer);color:#ccc}
.footer .links{position:absolute;left:49px;top:22px;font-size:6.4px;display:flex}
.footer .links span{margin-right:25px}
.footer .copy{position:absolute;left:49px;top:39px;font-size:6.4px}
.social{position:absolute;top:20px;width:24px;height:24px;border-radius:50%;border:1px solid #999}
</style>
</head>
<body>

<div class="abs top-bar">
  <div class="item" style="left:372px">
    <svg width="9" height="7" viewBox="0 0 9 7"><rect width="9" height="7" rx="1" fill="#fff"/><path d="M0 0l4.5 4L9 0" stroke="#272d69" fill="none" stroke-width=".8"/></svg>
    Email: kestrelwaymassage@fernmail.net
  </div>
  <div class="item" style="left:524px">
    <svg width="8" height="8" viewBox="0 0 8 8"><path d="M1.5 0.5l1.5 1.8-1 1a5 5 0 0 0 2.7 2.7l1-1L7.5 6.5 6.5 7.5C3 7 1 5 .5 1.5z" fill="#fff"/></svg>
    Phone: (206) 555-0148
  </div>
  <div class="divider"></div>
  <svg class="abs" style="left:626px;top:8px" width="7" height="7" viewBox="0 0 7 7"><circle cx="3" cy="3" r="2.2" stroke="#fff" fill="none" stroke-width="1.1"/><path d="M4.6 4.6L6.6 6.6" stroke="#fff" stroke-width="1.2"/></svg>
</div>

<div class="abs header">
  <span class="nav active" style="left:325px">HOME</span>
  <span class="nav" style="left:368px">ABOUT US</span>
  <span class="nav" style="left:424px">SERVICES</span>
  <span class="nav" style="left:477px">NEWS</span>
  <span class="nav" style="left:518px">TESTIMONIALS</span>
  <span class="nav" style="left:590px">CONTACT US</span>
</div>

<div class="abs brand">KESTREL<br>WAY</div>

<section class="abs hero" role="img" aria-label="Therapist giving a back massage to a client"></section>
<h1 class="abs hero-title">KESTREL <span>WAY</span> MASSAGE</h1>
<p class="abs hero-text">A Seattle based mobile massage team, Paul and Lina. We specialize in integrated pain management and sports/medical massage, and we come to your home, office or hotel.</p>
<div class="abs hero-btn">CLICK HERE FOR MORE INFO</div>
<div class="abs dots"><span></span><span></span><span class="on"></span><span></span><span></span></div>

<form class="abs contact-form">
  <div class="head">CONTACT FORM</div>
  <div class="field" style="top:40px">Name: <i>*</i></div>
  <div class="field" style="top:67px">Email: <i>*</i></div>
  <div class="field" style="top:95px">Phone: <i>*</i></div>
  <div class="field" style="top:122px;height:52px">Message:</div>
  <div class="submit">SUBMIT <svg width="7" height="7" viewBox="0 0 7 7"><circle cx="3.5" cy="3.5" r="3" stroke="#fff" fill="none"/><path d="M2.3 3.5h2.4M3.7 2.4l1.1 1.1-1.1 1.1" stroke="#fff" fill="none" stroke-width=".8"/></svg></div>
</form>

<section class="abs welcome">
  <h2 class="section-title" style="top:24px">WELCOME TO KESTREL WAY MASSAGE</h2>
  <p class="section-text" style="top:46px">Our massage is offered to the community with a goal of facilitating balance within each individual. Every client's first assessment is attended by both of us, our male and female therapist team.</p>

  <div class="card blue" style="left:50px">
    <div class="photo" role="img" aria-label="Neuromuscular massage on a client's back"></div>
    <div class="body"><h3>Neuromuscular</h3><p>Focused pressure on trigger points to ease pain and restore balance in the muscles.</p><div class="more">Read More &#8853;</div></div>
  </div>
  <div class="card navy" style="left:198px">
    <div class="photo" role="img" aria-label="Myofascial release on the shoulder"></div>
    <div class="body"><h3>Myofascial Release</h3><p>Gentle sustained work on the fascia to free tension and improve range of motion.</p><div class="more">Read More &#8853;</div></div>
  </div>
  <div class="card blue" style="left:346px">
    <div class="photo" role="img" aria-label="Spontaneous release massage on a leg"></div>
    <div class="body"><h3>Spontaneous</h3><p>Spontaneous muscle release that lets the body let go of guarding and deep pain.</p><div class="more">Read More &#8853;</div></div>
  </div>
  <div class="card navy" style="left:494px">
    <div class="photo" role="img" aria-label="Therapist stretching a client's leg"></div>
    <div class="body"><h3>Muscle Release</h3><p>Stretching and postural restoration to support lasting realignment and strength.</p><div class="more">Read More &#8853;</div></div>
  </div>
</section>

<section class="abs rates">
  <h2 class="section-title" style="top:21px">OUR RATEING</h2>
  <p class="section-text" style="top:46px">We bring the table to you, anywhere in Seattle. Depending on the goals identified in your first assessment, Paul, Lina or both of us will be assigned to provide your treatment.</p>
  <p class="rate-line">Our rates are <b>$75/ 60</b> minutes, <b>$95/ 90</b> minutes, and <b>$120/ 120</b> minutes.</p>
</section>

<section class="abs reviews">
  <h2 class="section-title" style="top:17px;color:#fff">5/5 STARS MASSAGE THERAPY</h2>
  <p class="section-text" style="top:37px">Progress should be tangible, such as range of motion and decreased pain. Here is what our clients say about working with Paul and Lina at Kestrel Way.</p>

  <div class="avatar" style="left:54px" role="img" aria-label="Client portrait"></div>
  <div class="reviewer" style="left:37px">NAME : NORA HALE</div>
  <div class="stars" style="left:37px">★★★★☆</div>
  <div class="quote" style="left:133px"><span class="q" style="left:8px;top:2px">“</span>Lina worked on me to increase my range of motion after surgery. They are the best therapists I have ever worked with.<span class="q" style="left:170px;top:38px">”</span></div>

  <div class="avatar" style="left:365px" role="img" aria-label="Client portrait"></div>
  <div class="reviewer" style="left:348px">NAME : OWEN PRYCE</div>
  <div class="stars" style="left:348px">★★★★☆</div>
  <div class="quote" style="left:443px"><span class="q" style="left:8px;top:2px">“</span>Paul has helped decrease my neck and lower back pain immensely. Professional, upbeat and always on time.<span class="q" style="left:170px;top:38px">”</span></div>
</section>

<section class="abs news">
  <h2>LATEST NEWS</h2>
  <div class="thumb"><div role="img" aria-label="Therapist massaging a client's back"></div></div>
  <h3>Postural restoration: how it fits into every massage treatment</h3>
  <p>We are both graduates of Venmora, school of massage therapy, with continuing education in medical massage, myofascial release, trigger point therapy, postural restoration, anatomy and spontaneous muscle release. Lina is also a Certified Yoga Instructor, and Paul brings stretching and strength training to encourage postural restoration and realignment.</p>
  <div class="date"><svg width="7" height="7" viewBox="0 0 7 7"><rect x=".5" y="1" width="6" height="5.5" fill="none" stroke="#272d69" stroke-width=".8"/><path d="M.5 2.6h6" stroke="#272d69" stroke-width=".8"/></svg>Sep 12 2015</div>
</section>

<footer class="abs footer">
  <div class="links"><span>HOME</span><span>ABOUT US</span><span>SERVICES</span><span>NEWS</span><span>TESTIMONIALS</span><span>CONTACT US</span></div>
  <div class="copy">Copyright © 2015 &nbsp;Kestrel Way Massage And Terms and Conditions</div>
  <div class="social" style="left:506px"></div>
  <div class="social" style="left:538px"></div>
  <div class="social" style="left:570px"></div>
  <div class="social" style="left:602px"></div>
</footer>

</body>
</html>
```